Website design for legal tech start up in Switzerland (B2B)

We are for a legal tech start up in Switzerland called KOVA. We have been running since August 2016. This will be our first live website.

We need a website designed and business card design for our start-up in Switzerland. We also need the Web design to be converted into HTML and CSS files.

Function of website:
• To inform potential customers of our services
• Form a key part of our digital marketing and sales footprint.
• Branding

Please find attached logo.
Updates

Project Deadline Extended Reason: Giving us time to review submissions and provide opportunity for more submissions. Added Thursday, February 16, 2017

Project Deadline Extended
Reason: Looking for more idea's not necessarily set on blue and grey colours only.

Target Market(s)

B2B tech powered legal services.

Industry/Entity Type

Legal

Contact Information for Business Card

Lean and slick design.

Coding

Coded - Design and coding required

Number of Pages Required

5+ page

Requirements
Must have
• VERY LEAN AND CLEAN DESIGN!
• We have received many great standard designs, but we are looking for something more out-of-the box: You can get inspiration from these designs: http://www.pixelvane.com/websites/clean/
• Thanks!!
• Easy content management system
• Well structured coding for additional development
• Responsive webpage for all types of devices
• SEO optimized
• Tabs (Home, services, team, careers, blog, contact us)
• Colour scheme complementary to logo
Nice to have
• Look and Design - Approachable, High-tech, Modern
• Easy to add chat bot capability in future
Should not have
• Too busy/ too much clutter
• Not take to long to load

```html
<!DOCTYPE html>
<html lang="en">
<head>
<meta charset="utf-8">
<title>KOVA — Legal Startup</title>
<link rel="stylesheet" href="https://fonts.googleapis.com/css2?family=Nunito:wght@300;400;600;700;800&display=swap">
<style>
:root{
  --navy:#1c3a6b;
  --navy-deep:#16305a;
  --ink:#333a44;
  --muted:#6f747b;
  --line:#d7d9dc;
  --paper:#ffffff;
  --foot:#f1f1f1;
}
*{box-sizing:border-box;margin:0;padding:0}
html,body{width:1200px;height:2177px;overflow:hidden}
body{font-family:'Nunito',sans-serif;color:var(--ink);background:var(--paper);position:relative}
.topbar{height:38px;background:var(--navy);color:#fff;display:flex;align-items:center;justify-content:space-between;padding:0 87px;font-size:14px}
.topbar .contact{display:flex;gap:24px;align-items:center}
.topbar .contact span{display:flex;align-items:center;gap:8px}
.topbar .social{display:flex;gap:8px}
.topbar .social i{width:17px;height:17px;border-radius:3px;background:#fff;display:block}
.header{height:93px;display:flex;align-items:center;justify-content:space-between;padding:0 58px 0 87px;box-shadow:0 2px 6px rgba(0,0,0,.08);position:relative;z-index:2}
.brand{font-size:54px;font-weight:800;color:var(--ink);letter-spacing:2px;line-height:1}
.nav{display:flex;list-style:none;font-size:16px;font-weight:400;text-transform:uppercase}
.nav li{padding:5px 19px;margin-left:15px;color:var(--ink)}
.nav li.active{border:1px solid var(--navy);border-radius:18px;color:var(--navy)}
.hero{height:512px;background:linear-gradient(180deg,#7d93aa 0%,#6e7f73 30%,#4f6a5e 55%,#3f6156 75%,#4e5a4a 100%);position:relative}
.hero-copy{position:absolute;left:87px;top:278px;color:#fff}
.hero h1{font-size:50px;font-weight:600;line-height:1.1}
.hero p{font-size:29px;font-weight:600;line-height:1.2}
.hero .arrows{display:flex;gap:2px;margin-top:18px}
.hero .arrows span{width:24px;height:28px;background:rgba(0,0,0,.55);display:flex;align-items:center;justify-content:center}
.welcome{text-align:center;padding-top:58px;height:492px}
.welcome h2{font-size:31px;font-weight:400;color:var(--navy);letter-spacing:.5px}
.welcome .intro{width:968px;margin:12px auto 0;font-size:14px;line-height:21px;color:var(--muted)}
.features{display:flex;justify-content:center;gap:46px;margin-top:56px}
.feature{width:218px;text-align:center}
.feature .ring{width:110px;height:110px;border-radius:50%;margin:0 auto;border:5px solid #f0f0f0;box-shadow:0 1px 6px rgba(0,0,0,.12);display:flex;align-items:center;justify-content:center;background:#fff}
.feature h3{font-size:17px;font-weight:400;margin-top:20px;text-transform:uppercase;color:var(--ink)}
.feature p{font-size:11px;line-height:17px;color:var(--muted);margin-top:10px}
.what{height:377px;background:linear-gradient(100deg,#24467a 0%,#2a4d82 45%,#213f70 100%);position:relative;color:#fff}
.what-copy{position:absolute;left:87px;top:76px;width:522px}
.what h2{font-size:26px;font-weight:400;letter-spacing:.5px}
.what p{font-size:12.5px;line-height:21px;margin-top:10px;text-align:justify;letter-spacing:-.15px}
.btn-ghost{display:inline-block;margin-top:20px;border:1px solid #fff;border-radius:18px;padding:8px 16px;font-size:12px;text-transform:uppercase}
.video{position:absolute;left:638px;top:56px;width:471px;height:275px;background:linear-gradient(180deg,#7d7fa3 0%,#c89a8e 35%,#8b7f7a 60%,#3c4654 100%);box-shadow:0 6px 18px rgba(0,0,0,.35);display:flex;align-items:center;justify-content:center}
.news{height:378px;padding-top:70px}
.news h2{text-align:center;font-size:31px;font-weight:400;color:#222}
.news-list{display:flex;margin-top:40px;padding-left:90px}
.story{display:flex;width:540px}
.story .thumb{width:162px;height:142px;flex:none}
.story .body{margin-left:15px;width:310px}
.story h4{font-size:13px;font-weight:600;color:#222;margin-top:8px}
.story time{display:block;font-size:12px;color:#444;margin-top:7px}
.story p{font-size:11px;line-height:19px;color:#555;margin-top:5px}
.story a{font-size:11px;color:var(--navy);text-decoration:none;display:block;margin-top:7px}
.footer{position:absolute;left:0;top:1894px;width:1200px;height:283px;background:var(--foot)}
.footer h5{font-size:14px;font-weight:400;color:#333;text-transform:uppercase;letter-spacing:.3px}
.col{position:absolute;top:54px}
.col p,.col li{font-size:11px;line-height:21px;color:#777}
.col ul{list-style:none;margin-top:14px}
.col ul li::before{content:"";display:inline-block;border-left:4px solid #555;border-top:3px solid transparent;border-bottom:3px solid transparent;margin-right:6px;vertical-align:1px}
.signup{display:flex;margin-top:8px}
.signup .field{width:146px;height:32px;border:1px solid #ccc;background:#fff;font-size:11px;color:#888;padding:9px 8px}
.signup .submit{width:57px;height:32px;background:var(--navy-deep);color:#fff;font-size:12px;display:flex;align-items:center;justify-content:center}
.follow{display:flex;gap:14px;margin-top:26px}
.follow i{width:24px;height:24px;border-radius:4px;background:#555;display:block}
.rule{position:absolute;left:90px;top:219px;width:1020px;border-top:1px solid #c9c9c9}
.copyright{position:absolute;top:245px;width:100%;text-align:center;font-size:12px;color:#333}
</style>
</head>
<body>
<div class="topbar">
  <div class="contact">
    <span><svg width="13" height="13" viewBox="0 0 24 24"><path fill="#fff" d="M6.6 10.8a15 15 0 006.6 6.6l2.2-2.2c.3-.3.7-.4 1-.2 1.1.4 2.3.6 3.6.6.6 0 1 .4 1 1V20c0 .6-.4 1-1 1A17 17 0 013 4c0-.6.4-1 1-1h3.5c.6 0 1 .4 1 1 0 1.3.2 2.5.6 3.6.1.3 0 .7-.2 1z"/></svg>555-014-2290</span>
    <span><svg width="14" height="11" viewBox="0 0 24 18"><rect width="24" height="18" rx="2" fill="#fff"/><path d="M1 2l11 8 11-8" stroke="#1c3a6b" stroke-width="2" fill="none"/></svg>info@kovalegal.ch</span>
  </div>
  <div class="social"><i></i><i></i><i></i><i></i><i></i></div>
</div>

<header class="header">
  <div class="brand">KOVA</div>
  <ul class="nav">
    <li class="active">Home</li><li>Services</li><li>Team</li><li>Careers</li><li>Blog</li><li>Contact Us</li>
  </ul>
</header>

<section class="hero" role="img" aria-label="Aerial photo of a Swiss lakeside city with river, bridges and mountains">
  <div class="hero-copy">
    <h1>LEGAL STARTUP</h1>
    <p>Neque porro quisquam est qui</p>
    <div class="arrows">
      <span><svg width="8" height="14" viewBox="0 0 8 14"><path d="M7 1L1 7l6 6" stroke="#fff" fill="none" stroke-width="1.5"/></svg></span>
      <span><svg width="8" height="14" viewBox="0 0 8 14"><path d="M1 1l6 6-6 6" stroke="#fff" fill="none" stroke-width="1.5"/></svg></span>
    </div>
  </div>
</section>

<section class="welcome">
  <h2>WELCOME TO KOVA</h2>
  <p class="intro">It is a long established fact that a reader will be distracted by the readable content of a page when looking at its layout. The point of using Lorem Ipsum is that it has a more-or-less normal distribution of letters, as opposed to using 'Content here, content here', making it look like readable English.</p>
  <div class="features">
    <div class="feature">
      <div class="ring"><svg width="42" height="38" viewBox="0 0 42 38"><rect x="1" y="1" width="40" height="27" rx="2" fill="#1c3a6b"/><rect x="5" y="5" width="32" height="19" fill="#fff"/><rect x="17" y="28" width="8" height="6" fill="#1c3a6b"/><rect x="11" y="33" width="20" height="4" rx="1" fill="#1c3a6b"/></svg></div>
      <h3>Porro Quisquam</h3>
      <p>It has survived not only five centuries, but also the leap into electronic typesetting, remaining essentially unchanged.</p>
    </div>
    <div class="feature">
      <div class="ring"><svg width="38" height="38" viewBox="0 0 38 38"><path fill="#1c3a6b" d="M4 10h9a5 5 0 1110 0h9v9a5 5 0 110 10v7H23a5 5 0 10-10 0H4V26a5 5 0 100-10z"/></svg></div>
      <h3>Quisquam Est</h3>
      <p>It has survived not only five centuries, but also the leap into electronic typesetting, remaining essentially unchanged.</p>
    </div>
    <div class="feature">
      <div class="ring"><svg width="42" height="40" viewBox="0 0 42 40"><circle cx="16" cy="22" r="10" fill="none" stroke="#1c3a6b" stroke-width="6" stroke-dasharray="4 3"/><circle cx="16" cy="22" r="7" fill="none" stroke="#1c3a6b" stroke-width="4"/><circle cx="32" cy="10" r="6" fill="none" stroke="#1c3a6b" stroke-width="4" stroke-dasharray="3 2"/><circle cx="33" cy="31" r="5" fill="none" stroke="#1c3a6b" stroke-width="4" stroke-dasharray="3 2"/></svg></div>
      <h3>Dolorem Ipsum</h3>
      <p>It has survived not only five centuries, but also the leap into electronic typesetting, remaining essentially unchanged.</p>
    </div>
    <div class="feature">
      <div class="ring"><svg width="36" height="36" viewBox="0 0 36 36"><rect width="36" height="36" rx="6" fill="#1c3a6b"/><path d="M10 26l2-6 12-12 4 4-12 12z" fill="#fff"/></svg></div>
      <h3>Quisquam</h3>
      <p>It has survived not only five centuries, but also the leap into electronic typesetting, remaining essentially unchanged.</p>
    </div>
  </div>
</section>

<section class="what">
  <div class="what-copy">
    <h2>WHAT WE DO</h2>
    <p>It has survived not only five centuries, but also the leap into electronic typesetting, remaining essentially unchanged. It was popularised in the 1960s with the release of Fontwell sheets containing Lorem Ipsum passages, and more recently with desktop publishing software like Vellum Layout including versions of Lorem Ipsum It has survived not only five centuries, but also the leap into electronic typesetting, remaining essentially unchanged. It was popularised in the 1960s with the release of Fontwell sheets containing Lorem Ipsum passages, and more recently with desktop publishing software</p>
    <span class="btn-ghost">Read More</span>
  </div>
  <div class="video" role="img" aria-label="Video still of an old town riverside with a stone bridge and church spire at dusk">
    <svg width="54" height="54" viewBox="0 0 54 54"><circle cx="27" cy="27" r="27" fill="rgba(40,40,40,.75)"/><path d="M21 16l17 11-17 11z" fill="#fff"/></svg>
  </div>
</section>

<section class="news">
  <h2>LATEST NEWS</h2>
  <div class="news-list">
    <article class="story">
      <div class="thumb" role="img" aria-label="Photo of a lakeside old town with red roofs" style="background:linear-gradient(180deg,#9fb4c8 0%,#b58a74 45%,#8a5a48 100%)"></div>
      <div class="body">
        <h4>Neque porro quisquam</h4>
        <time>09-07-2017</time>
        <p>Lorem Ipsum has been the industry's standard dummy text ever since the 1500s, when an unknown printer took a galley of type and scrambled it to make a type specimen book.</p>
        <a href="#">Read More &gt;&gt;</a>
      </div>
    </article>
    <article class="story">
      <div class="thumb" role="img" aria-label="Photo of a harbour with boats and church towers under blue sky" style="background:linear-gradient(180deg,#4f8fd0 0%,#a9c3d8 45%,#a69a84 70%,#4f7f9a 100%)"></div>
      <div class="body">
        <h4>Neque porro quisquam</h4>
        <time>09-07-2017</time>
        <p>Lorem Ipsum has been the industry's standard dummy text ever since the 1500s, when an unknown printer took a galley of type and scrambled it to make a type specimen book.</p>
        <a href="#">Read More &gt;&gt;</a>
      </div>
    </article>
  </div>
</section>

<footer class="footer">
  <div class="col" style="left:94px">
    <h5>Contact Us</h5>
    <p style="margin-top:16px">Address : 12 Seefeld Strasse, Zurich<br>8008, Switzerland<br>Phone : 555-019-7731.<br>Email : info@kovalegal.ch</p>
  </div>
  <div class="col" style="left:419px">
    <h5>Navigate</h5>
    <ul><li>ABOUT US</li><li>SERVICES</li><li>SUPPORT</li><li>NEWS</li></ul>
  </div>
  <div class="col" style="left:630px">
    <h5>Join Our Mailing List</h5>
    <p style="margin-top:16px;width:190px;line-height:17px">Your about us information would fit here nicely.</p>
    <div class="signup"><span class="field">Email address</span><span class="submit">Submit</span></div>
  </div>
  <div class="col" style="left:937px">
    <h5>Follow Us Out There</h5>
    <div class="follow"><i></i><i></i><i></i><i></i></div>
  </div>
  <div class="rule"></div>
  <p class="copyright">Copyright © 2017. All Rights Reserved</p>
</footer>
</body>
</html>
```